Varnex Consulting Business card design.

See our website www.varnexconsulting.example which will give you a good idea of what we are about. The font is called 'Play'.

I'd like a standout business card in keeping with the themes and branding on the website

Target Market(s)

professionals. HR directors

Industry/Entity Type

Business

Contact Information for Business Card

Varnex Consulting PO Box 3172 Merrowdale NSW 2291 1300 485 193 Gavin Threlkeld Principal email: career@varnexconsulting.example ABN: 71203948865

Font styles to use
Other font styles liked:
• Play

Requirements
Must have
• Must have same design colours and branding as website.
• On back I'd prefer a list of the things we do which appears below the name at the header on the website

```html
<!DOCTYPE html>
<html lang="en">
<head>
<meta charset="utf-8">
<title>Varnex Consulting – Business Card</title>
<link href="https://fonts.googleapis.com/css2?family=Play:wght@400&display=swap" rel="stylesheet">
<style>
  :root {
    --page-bg: #e9e6e1;
    --navy-top: #123553;
    --navy-bottom: #0a1e32;
    --sky: #4ab4e2;
    --sky-soft: #5aa9cf;
    --white: #ffffff;
    --rule: rgba(255,255,255,0.75);
    --photo-light: #eef0f1;
    --photo-mid: #b9bec2;
    --photo-dark: #6f7579;
    --band: rgba(255,255,255,0.55);
  }
  * { box-sizing: border-box; margin: 0; padding: 0; }
  html, body { width: 1200px; height: 892px; overflow: hidden; }
  body {
    background: var(--page-bg);
    font-family: 'Play', sans-serif;
    display: flex;
    flex-direction: column;
    align-items: center;
    justify-content: center;
    gap: 36px;
  }
  .card {
    position: relative;
    width: 700px;
    height: 400px;
    border-radius: 24px;
    overflow: hidden;
    box-shadow: 0 6px 18px rgba(0,0,0,0.18);
  }

  /* Front */
  .card-front {
    background: linear-gradient(160deg, var(--navy-top), var(--navy-bottom));
    color: var(--white);
  }
  .brand {
    position: absolute;
    left: 48px;
    top: 50px;
    font-size: 48px;
    font-weight: 400;
    letter-spacing: 1px;
    line-height: 1;
    color: var(--white);
  }
  .services {
    position: absolute;
    left: 50px;
    top: 116px;
    font-size: 15px;
    letter-spacing: 2px;
    color: var(--sky-soft);
  }
  .services .sep { opacity: 0.7; margin: 0 4px; }
  .divider {
    position: absolute;
    left: 48px;
    right: 36px;
    top: 180px;
    display: flex;
    align-items: center;
    gap: 10px;
  }
  .divider .line { height: 1px; background: var(--rule); }
  .divider .line-long { flex: 1; }
  .divider .line-short { width: 50px; }
  .abn { font-size: 20px; letter-spacing: 1px; white-space: nowrap; }
  .person {
    position: absolute;
    left: 48px;
    bottom: 46px;
  }
  .person-name { font-size: 26px; color: var(--sky); }
  .person-role { font-size: 22px; margin-top: 2px; }
  .contacts {
    position: absolute;
    right: 40px;
    top: 214px;
    list-style: none;
    font-size: 19px;
    line-height: 1.6;
  }
  .contacts li { display: flex; align-items: center; gap: 12px; white-space: nowrap; }
  .contacts svg { width: 18px; height: 18px; fill: var(--sky); flex: none; }

  /* Back */
  .card-back { background: var(--photo-light); }
  .back-photo {
    position: absolute;
    inset: 0;
    background:
      radial-gradient(ellipse at 78% 55%, var(--photo-dark) 0%, rgba(111,117,121,0) 38%),
      radial-gradient(ellipse at 25% 60%, var(--photo-light) 0%, rgba(238,240,241,0) 55%),
      linear-gradient(135deg, var(--photo-light), var(--photo-mid));
  }
  .back-band {
    position: absolute;
    left: 0;
    right: 0;
    top: 140px;
    height: 120px;
    background: var(--band);
  }
  .back-brand {
    position: absolute;
    left: 48px;
    top: 164px;
    font-size: 46px;
    font-weight: 400;
    letter-spacing: 1px;
    line-height: 1;
    color: var(--sky);
  }
  .back-services {
    position: absolute;
    left: 50px;
    top: 222px;
    font-size: 15px;
    letter-spacing: 2px;
    color: var(--sky-soft);
  }
</style>
</head>
<body>

  <section class="card card-front" aria-label="Business card front">
    <h1 class="brand">Varnex Consulting</h1>
    <p class="services">Search &amp; Select<span class="sep">|</span>Career<span class="sep">|</span>Coaching<span class="sep">|</span>Leadership<span class="sep">|</span>Outplacement</p>

    <div class="divider">
      <span class="line line-long"></span>
      <span class="abn">ABN: 71203948865</span>
      <span class="line line-short"></span>
    </div>

    <div class="person">
      <p class="person-name">Gavin Threlkeld</p>
      <p class="person-role">Principal</p>
    </div>

    <ul class="contacts">
      <li>
        <svg viewBox="0 0 24 24" aria-hidden="true"><path d="M6.6 10.8a15.1 15.1 0 0 0 6.6 6.6l2.2-2.2a1 1 0 0 1 1-.25 11.4 11.4 0 0 0 3.6.57 1 1 0 0 1 1 1V20a1 1 0 0 1-1 1A17 17 0 0 1 3 4a1 1 0 0 1 1-1h3.5a1 1 0 0 1 1 1c0 1.25.2 2.45.57 3.57a1 1 0 0 1-.25 1z"/></svg>
        1300 485 193
      </li>
      <li>
        <svg viewBox="0 0 24 24" aria-hidden="true"><path d="M2 5h20v14H2z"/><path d="M2 5l10 8 10-8" fill="none" stroke="#0e2a45" stroke-width="1.6"/></svg>
        career@varnexconsulting.example
      </li>
      <li>
        <svg viewBox="0 0 24 24" aria-hidden="true"><path d="M12 2a7 7 0 0 0-7 7c0 5.2 7 13 7 13s7-7.8 7-13a7 7 0 0 0-7-7zm0 9.5A2.5 2.5 0 1 1 12 6.5a2.5 2.5 0 0 1 0 5z"/></svg>
        PO Box 3172 Merrowdale NSW 2291
      </li>
    </ul>
  </section>

  <section class="card card-back" aria-label="Business card back">
    <div class="back-photo" role="img" aria-label="Photograph of a surfer in a black wetsuit riding white water on a surfboard"></div>
    <div class="back-band"></div>
    <h2 class="back-brand">Varnex Consulting</h2>
    <p class="back-services">Search &amp; Select | Career | Coaching | Leadership | Outplacement</p>
  </section>

</body>
</html>
```